4D Cradle Glimpse Luxury Ultrasound Billboard

Design a HIGH-END, MODERN billboard for my private prenatal ultrasound studio, 4D Cradle Glimpse, located in Pace, Florida.
This billboard will be viewed by drivers traveling at highway speeds, so it must be extremely clean, simple, and readable within 6 seconds.
About My Business
4D Cradle Glimpse is a private prenatal ultrasound studio specializing in:
Highest technology 4D/HD Ultrasounds
Early Gender Determination
Pregnancy Confirmation
I have been serving families for nearly 10 years and is known for creating a memorable experience, not just an ultrasound appointment.
Design Style
I DO NOT want:
Flowers
Leaves
Swirls
Glitter
Hearts everywhere
Busy backgrounds
Generic maternity stock graphics
I DO want:
Modern
Luxury
Upscale
Clean
Professional
Eye-catching
Premium medical spa feel
Colors
Use colors from my logo:
LOGO Green ( or a deep green)
Black
White
Soft Gold accents
Images:
Incorporate my professional headshot in a clean, modern way, logo, and the ultrasound images
Text
Keep wording minimal.
Primary Headline ( OPEN TO IDEAS) :
EXAMPLES ( WOULD RATHER SOMETHING MORE CATCHY)
" ADVANCED IMAGING. UNFORGETTABLE MOMENTS"
"MEET YOUR BABY BEFORE BIRTH"
Under headline:
4D Ultrasound • Early Gender • Pregnancy Confirmation
Business Name:
4D Cradle Glimpse
Private Prenatal Ultrasound Studio
Phone Number:
850-471-5923
Important
This billboard must be readable in 5–6 seconds from a moving vehicle.
Less text is better.
The phone number and business name must be visible from a distance.
The design should feel like a premium brand that immediately tells expecting parents:
“This is where I go to see my baby.”
Files Provided
Official logo
Headshot
Ultrasound images
Don’t make this look like a medical office billboard.
Make it look like a luxury baby experience billboard. That’s what separates 4D Cradle Glimpse from hospitals, OB offices, and all the new studios popping up around you. The emotional connection is what gets moms to book. ❤️
Billboard Size - 10.6” x 36”

```html
<!DOCTYPE html>
<html lang="en">
<head>
<meta charset="utf-8">
<title>4D Cradle Glimpse Billboard</title>
<link href="https://fonts.googleapis.com/css2?family=Archivo:wght@600;700;800&family=Roboto+Condensed:wght@800&display=swap" rel="stylesheet">
<style>
  :root {
    --page: #ffffff;
    --board: #ffffff;
    --gold: #c8993a;
    --slate: #5f716a;
    --slate-text: #596a64;
    --white: #ffffff;
    --edge: #2a2a2a;
  }
  html, body {
    margin: 0;
    width: 1200px;
    height: 876px;
    overflow: hidden;
    background: var(--page);
  }
  .billboard {
    position: absolute;
    left: 20px;
    top: 267px;
    width: 1160px;
    height: 342px;
    display: block;
  }
  .headline { font-family: "Archivo", Arial, sans-serif; font-weight: 800; }
  .headline-top { fill: var(--gold); }
  .headline-bottom { fill: var(--slate-text); }
  .services { font-family: "Archivo", Arial, sans-serif; font-weight: 700; fill: var(--slate-text); }
  .phone { font-family: "Roboto Condensed", "Arial Narrow", sans-serif; font-weight: 800; fill: var(--white); }
  .brand-name { font-family: "Archivo", Arial, sans-serif; font-weight: 600; fill: var(--white); }
  .brand-tagline { font-family: "Archivo", Arial, sans-serif; font-weight: 600; fill: var(--white); }
</style>
</head>
<body>
<svg class="billboard" viewBox="0 0 1160 342" xmlns="http://www.w3.org/2000/svg">
  <defs>
    <linearGradient id="portraitTone" x1="0" y1="0" x2="1" y2="1">
      <stop offset="0" stop-color="#eeece8"/>
      <stop offset="0.35" stop-color="#d8c3a0"/>
      <stop offset="0.65" stop-color="#3f5a3f"/>
      <stop offset="1" stop-color="#2f3f33"/>
    </linearGradient>
    <radialGradient id="scanTone" cx="0.45" cy="0.45" r="0.6">
      <stop offset="0" stop-color="#e0a48e"/>
      <stop offset="0.6" stop-color="#b5604a"/>
      <stop offset="1" stop-color="#5a2418"/>
    </radialGradient>
    <linearGradient id="ruleFade" x1="0" y1="0" x2="1" y2="0">
      <stop offset="0" stop-color="#c8993a" stop-opacity="0"/>
      <stop offset="0.15" stop-color="#c8993a"/>
      <stop offset="0.85" stop-color="#c8993a"/>
      <stop offset="1" stop-color="#c8993a" stop-opacity="0"/>
    </linearGradient>
    <clipPath id="portraitClip">
      <path d="M0,0 H205 C245,40 262,130 240,200 C225,250 195,300 155,342 H0 Z"/>
    </clipPath>
  </defs>

  <rect class="board" x="0" y="0" width="1160" height="342" fill="var(--board)"/>

  <path class="contact-band" d="M0,0 H213 C255,40 272,130 250,200 C242,225 232,245 222,260 H1160 V342 H0 Z" fill="var(--slate)"/>

  <rect class="portrait" x="0" y="0" width="270" height="342" fill="url(#portraitTone)" clip-path="url(#portraitClip)" role="img" aria-label="Portrait of the studio owner in green scrubs holding an ultrasound probe"/>

  <circle class="scan-image" cx="279" cy="210" r="85" fill="url(#scanTone)" stroke="var(--gold)" stroke-width="2" role="img" aria-label="4D ultrasound image of a baby's face"/>

  <text class="headline headline-top" x="320" y="91" font-size="100" textLength="812" lengthAdjust="spacingAndGlyphs">MEET YOUR BABY</text>
  <text class="headline headline-bottom" x="387" y="170" font-size="100" textLength="675" lengthAdjust="spacingAndGlyphs">BEFORE BIRTH</text>

  <rect class="gold-rule" x="363" y="179" width="745" height="1.5" fill="url(#ruleFade)"/>

  <text class="services" x="425" y="215" font-size="25" textLength="599" lengthAdjust="spacingAndGlyphs">• 4D ULTRASOUND • EARLY GENDER</text>
  <text class="services" x="471" y="249" font-size="25" textLength="507" lengthAdjust="spacingAndGlyphs">• PREGNANCY CONFIRMATION</text>

  <text class="phone" x="341" y="323" font-size="68" textLength="421" lengthAdjust="spacingAndGlyphs">850-471-5923</text>
  <rect class="divider" x="780" y="271" width="2" height="53" fill="var(--white)"/>
  <text class="brand-name" x="800" y="305" font-size="36" textLength="335" lengthAdjust="spacingAndGlyphs">4D Cradle Glimpse</text>
  <text class="brand-tagline" x="800" y="324" font-size="13" textLength="335" lengthAdjust="spacingAndGlyphs">PRIVATE PRENATAL ULTRASOUND STUDIO</text>

  <rect class="board-edge" x="0.5" y="0.5" width="1159" height="341" fill="none" stroke="var(--edge)" stroke-width="1"/>
</svg>
</body>
</html>
```